business card for horse saddlery

after a new business card for our saddlery, i will add 2 logos we have previously used and they can be used (or not) . Any images can be used from our website also at www.harrowfields.net.au, I have also added our brand logo, which may be good to incorporate on back ? we have over 15, 000 items online, ship Australia Wide.

Target Market(s)

horse owners

Industry/Entity Type

Retail - Equestrian

Contact Information for Business Card

Harrowfield Horse Supplies, 1300 48 62 90, www.harrowfields.net.au, 27 Lindqvist Rd Marrowbank Q 4587

Requirements
Must have
• trailgem is our brand so trailgem logo on back as 'distributers of', easy to read
Nice to have
• professional but fun
Should not have
• double sided (description wont save double sided)

```html
<!DOCTYPE html>
<html lang="en">
<head>
<meta charset="utf-8">
<title>Harrowfield Horse Supplies – Business Card</title>
<link href="https://fonts.googleapis.com/css2?family=Poppins:wght@400;500;600&display=swap" rel="stylesheet">
<style>
  :root {
    --navy: #0d2d7a;
    --royal: #0c3a8c;
    --gold: #f8b31b;
    --ink: #1d1d1f;
    --rule: #d4d7de;
    --arc-grey: #bdbdbd;
    --paper: #ffffff;
    --backdrop: #eeeeee;
  }
  * { box-sizing: border-box; margin: 0; padding: 0; }
  html, body {
    width: 1134px; height: 1200px; overflow: hidden;
    background: var(--backdrop);
    font-family: "Poppins", sans-serif;
  }
  .sheet {
    position: relative; width: 1134px; height: 1200px;
  }
  .card {
    position: absolute; left: 117px; width: 900px; height: 514px;
    background: var(--paper);
    box-shadow: 0 10px 28px rgba(0,0,0,0.18);
    overflow: hidden;
  }
  .card--front { top: 52px; }
  .card--back { top: 630px; }
  .card svg.art { position: absolute; inset: 0; }

  /* front */
  .brand-mark {
    position: absolute; left: 72px; top: 140px;
  }
  .brand-mark__sun {
    width: 104px; height: 104px; border-radius: 50%;
    background: var(--gold); margin-left: 58px; margin-bottom: 10px;
  }
  .brand-mark__name {
    color: var(--navy); font-weight: 500; font-size: 42px; line-height: 1.1;
  }
  .web-line {
    position: absolute; font-size: 20px; letter-spacing: 6px; white-space: nowrap;
  }
  .web-line__domain { color: var(--gold); font-weight: 600; }
  .card--front .web-line { left: 66px; top: 440px; color: var(--ink); }

  /* back */
  .distributor {
    position: absolute; left: 102px; top: 95px;
    font-size: 23px; color: var(--ink);
  }
  .partner-mark {
    position: absolute; left: 104px; top: 250px;
    display: flex; align-items: center; gap: 16px;
  }
  .partner-mark__dot {
    width: 52px; height: 52px; border-radius: 50%; background: var(--royal);
  }
  .partner-mark__name {
    font-size: 46px; font-weight: 500; color: var(--ink); letter-spacing: 1px;
  }
  .divider {
    position: absolute; left: 441px; top: 120px; width: 1px; height: 205px;
    background: var(--rule);
  }
  .contact {
    position: absolute; left: 475px; top: 152px;
  }
  .contact__company {
    color: var(--navy); font-weight: 600; font-size: 25px; margin-bottom: 14px;
  }
  .contact__row {
    display: flex; align-items: flex-start; gap: 14px;
    font-size: 22px; color: var(--ink); line-height: 30px; margin-bottom: 8px;
  }
  .contact__icon { flex: 0 0 26px; height: 26px; margin-top: 2px; }
  .card--back .web-line {
    left: 0; width: 900px; text-align: center; top: 476px; color: #fff;
  }
</style>
</head>
<body>
<main class="sheet">

  <!-- Front -->
  <section class="card card--front" aria-label="Business card front">
    <svg class="art" viewBox="0 0 900 514" width="900" height="514" aria-hidden="false">
      <defs>
        <linearGradient id="photoTones" x1="0" y1="0" x2="1" y2="1">
          <stop offset="0" stop-color="#6f8a4a"/>
          <stop offset="0.35" stop-color="#7a3f1f"/>
          <stop offset="0.7" stop-color="#5a2a12"/>
          <stop offset="1" stop-color="#8a9a6a"/>
        </linearGradient>
      </defs>
      <path role="img" aria-label="Photo of a bay racehorse galloping in a blue bridle"
            d="M640,0 L900,0 L900,514 L650,514 C560,460 470,360 470,250 C470,140 540,50 640,0 Z"
            fill="url(#photoTones)"/>
      <path d="M612,0 C522,58 462,150 456,250" fill="none" stroke="var(--royal)" stroke-width="14"/>
      <path d="M482,362 C520,440 568,490 612,514" fill="none" stroke="var(--arc-grey)" stroke-width="14"/>
    </svg>
    <div class="brand-mark">
      <div class="brand-mark__sun"></div>
      <div class="brand-mark__name">Harrowfield<br>Horse Supplies</div>
    </div>
    <p class="web-line">www.<span class="web-line__domain">harrowfields</span>.net.au</p>
  </section>

  <!-- Back -->
  <section class="card card--back" aria-label="Business card back">
    <svg class="art" viewBox="0 0 900 514" width="900" height="514" aria-hidden="true">
      <path d="M0,446 Q470,382 900,452 L900,464 Q470,396 0,458 Z" fill="var(--gold)"/>
      <path d="M0,466 Q470,400 900,470 L900,514 L0,514 Z" fill="var(--royal)"/>
    </svg>
    <p class="distributor">Distributor of</p>
    <div class="partner-mark">
      <span class="partner-mark__dot"></span>
      <span class="partner-mark__name">Trailgem</span>
    </div>
    <div class="divider"></div>
    <div class="contact">
      <p class="contact__company">Harrowfield Horse Supplies</p>
      <div class="contact__row">
        <svg class="contact__icon" viewBox="0 0 26 26"><circle cx="13" cy="13" r="13" fill="var(--gold)"/><path d="M9 7.5l2.2-.4 1.2 3-1.4 1.1a7 7 0 0 0 3.2 3.2l1.1-1.4 3 1.2-.4 2.2c-4.6.4-9.3-4.3-8.9-8.9z" fill="none" stroke="#7a4b00" stroke-width="1.1" stroke-linejoin="round"/></svg>
        <span>1300 48 62 90</span>
      </div>
      <div class="contact__row">
        <svg class="contact__icon" viewBox="0 0 26 26"><circle cx="13" cy="13" r="13" fill="var(--gold)"/><path d="M13 20s-5-5-5-8.5a5 5 0 0 1 10 0C18 15 13 20 13 20z" fill="none" stroke="#7a4b00" stroke-width="1.2"/><circle cx="13" cy="11.5" r="1.8" fill="none" stroke="#7a4b00" stroke-width="1.2"/></svg>
        <span>27 Lindqvist Rd<br>Marrowbank Q 4587</span>
      </div>
      <div class="contact__row">
        <svg class="contact__icon" viewBox="0 0 26 26"><circle cx="13" cy="13" r="13" fill="var(--gold)"/><g fill="none" stroke="#7a4b00" stroke-width="1.1"><circle cx="13" cy="13" r="6"/><ellipse cx="13" cy="13" rx="2.6" ry="6"/><path d="M7 13h12M8 10h10M8 16h10"/></g></svg>
        <span>www.harrowfields.net.au</span>
      </div>
    </div>
    <p class="web-line">www.<span class="web-line__domain">harrowfields</span>.net.au</p>
  </section>

</main>
</body>
</html>
```